Modern Banner and Window Decal Design For Law Firm Lawyer

We are looking for three modern and sophisticated banner design and window decal for our law firm.

Banner measurements/types:

1) Height: 130 cm Width: 160 cm (Outdoor banner)
2) Height: 200 cm Width: 85 cm (Pull up/retractable indoor banner)

Window Decal:
3) Height: 70cm width 70cm

Our law firm is based in Melbourne, Australia and we deal with property law mostly.

We prefer a white background with classic text in black or grey. We would also like a dash of colour so please use a green, blue or aqua colour palette that is consistent with our logo. Vector attached. A nice photo of property, Melbourne city viee, or family home would be nice.

We do not want any law related images - scales of justice, gavel or the like.

Our ultimate goal is to communicate that the firm is modern, professional and knowledgeable

We would like the following:

1. Our logo
2. Our services: - Property Law - Wills - Powers of Attorney - Probate - Estate Administration - Consultancy & Agency
3. Phone number
4. Web Address

5. For pull up/retractable banner we would also like the following text:

We use the latest digital technology and fixed-fees to provide fast and affordable legal advice that is easy to understand.

For privacy reasons, we will provide business details once we have decided on the winner.

We will monitor entries closely and promise to provide feedback and guidance on each entry.

Thank you very much for considering this project.

Target Market(s)

General public, professionals, lawyers and conveyancers

Industry/Entity Type

Law Firm

Font styles to use
Sans Serif

Colors
0393ce
34a6d7
0456a4
3176b5
acd037
33b8a4
86cfc6
00a990
9ccb3b

Requirements
Must have
• 1. Our logo
• 2. Our services: - Property Law - Wills - Powers of Attorney - Probate & Estate Administration - Consultancy & Agency
• 3. Phone number
• 4. Web Address
Nice to have
• Picture of Melbourne, Australia city ; property/buildings/lawyers
Should not have
• We do not want any law related images - scales of justice, gavel or the like.

```html
<!DOCTYPE html>
<html lang="en">
<head>
<meta charset="UTF-8">
<title>Ridgeview Lawyers – Pull-up Banner</title>
<link href="https://fonts.googleapis.com/css2?family=Montserrat:wght@400;500;700&family=Roboto+Condensed:wght@400;700&display=swap" rel="stylesheet">
<style>
  :root {
    --page-bg: #ececec;
    --white: #ffffff;
    --panel-grey: #e6e6e7;
    --ink: #111111;
    --name-grey: #4f4f52;
    --navy: #0456a4;
    --blue: #0393ce;
    --sky: #34a6d7;
    --photo-sky-top: #4f93d6;
    --photo-sky-low: #a9cdea;
    --photo-city: #8c8a80;
    --photo-city-dark: #5d5f58;
    --photo-river: #233441;
    --photo-bank: #7a6650;
  }
  * { box-sizing: border-box; margin: 0; padding: 0; }
  html, body { width: 1200px; height: 1000px; overflow: hidden; }
  body { background: var(--page-bg); position: relative; font-family: "Montserrat", sans-serif; }

  .banner {
    position: absolute; left: 693px; top: 30px;
    width: 382px; height: 940px;
    background: var(--white);
    box-shadow: 0 6px 24px rgba(0,0,0,0.18);
    display: flex; flex-direction: column;
  }

  .brand {
    height: 190px; display: flex; align-items: center; justify-content: center; gap: 16px;
    padding-right: 6px;
  }
  .brand-dot { width: 84px; height: 84px; border-radius: 50%; background: var(--sky); flex: none; }
  .brand-name {
    font-family: "Montserrat", sans-serif; font-weight: 500; color: var(--name-grey);
    font-size: 28px; line-height: 1.15; letter-spacing: 0.6px;
  }
  .brand-name .line-two { font-size: 21px; letter-spacing: 1.6px; }

  .services { height: 140px; background: var(--panel-grey); position: relative; padding: 26px 0 0 20px; }
  .services-title {
    position: absolute; top: -12px; left: 50%; transform: translateX(-50%);
    background: var(--navy); color: var(--white);
    font-weight: 500; font-size: 19px; padding: 2px 14px; border-radius: 6px; white-space: nowrap;
    border: 2px solid var(--white);
  }
  .service-list { list-style: none; display: flex; flex-wrap: wrap; column-gap: 44px; row-gap: 7px; }
  .service-list li {
    font-weight: 700; font-size: 16.5px; color: var(--ink); display: flex; align-items: center; gap: 6px;
    text-transform: uppercase; white-space: nowrap; line-height: 19px;
  }
  .service-list li::before { content: ""; width: 6px; height: 6px; background: var(--blue); flex: none; }
  .service-list .full { flex-basis: 100%; }

  .stripe { height: 8px; background: var(--blue); }

  .city-photo {
    height: 468px;
    background: linear-gradient(180deg,
      var(--photo-sky-top) 0%,
      #78acdf 20%,
      var(--photo-sky-low) 40%,
      var(--photo-city) 52%,
      var(--photo-city-dark) 62%,
      #3e4f4a 66%,
      var(--photo-river) 72%,
      #1f2f3b 86%,
      #5c5a52 93%,
      var(--photo-bank) 100%);
  }

  .tagline {
    height: 50px; background: var(--sky); color: var(--white);
    font-family: "Roboto Condensed", sans-serif; font-size: 13.5px; text-align: center;
    display: flex; align-items: center; justify-content: center; padding: 0 18px; line-height: 1.3;
  }

  .contact {
    flex: 1; background: var(--blue); color: var(--white);
    display: flex; flex-direction: column; align-items: center; justify-content: center; gap: 0;
  }
  .phone { display: flex; align-items: center; gap: 8px; font-family: "Roboto Condensed", sans-serif; font-weight: 700; font-size: 33px; line-height: 1.1; }
  .phone svg { width: 28px; height: 28px; }
  .web { font-family: "Roboto Condensed", sans-serif; font-size: 20px; }
  .web strong { font-weight: 700; }
</style>
</head>
<body>
  <main class="banner">
    <header class="brand">
      <span class="brand-dot"></span>
      <span class="brand-name">RIDGEVIEW<br><span class="line-two">LAWYERS</span></span>
    </header>

    <section class="services">
      <h2 class="services-title">OUR SERVICES:</h2>
      <ul class="service-list">
        <li>Property Law</li>
        <li>Wills</li>
        <li class="full">Powers of Attorney</li>
        <li class="full">Probate &amp; Estate Administration</li>
        <li class="full">Consultancy &amp; Agency</li>
      </ul>
    </section>

    <div class="stripe"></div>

    <div class="city-photo" role="img" aria-label="Photo of the Melbourne city skyline with towers, a cathedral spire, a stone bridge and the river in the foreground"></div>

    <p class="tagline">We use the latest digital technology and fixed-fees to provide fast and affordable legal advice that is easy to understand.</p>

    <footer class="contact">
      <div class="phone">
        <svg viewBox="0 0 28 28" aria-hidden="true">
          <rect x="0" y="0" width="28" height="28" rx="6" fill="#ffffff"/>
          <path d="M9 6.5c.8-.4 1.6-.2 2 .6l1.4 2.8c.3.7.1 1.4-.5 1.8l-1 .7c.8 1.9 2.3 3.5 4.2 4.4l.8-1c.4-.6 1.2-.8 1.8-.4l2.7 1.5c.7.4.9 1.3.5 2l-.8 1.4c-.5.8-1.5 1.2-2.4.9C12.5 19.7 8.4 15.6 7 10.4c-.3-.9.1-1.9.9-2.4z" fill="#0393ce"/>
        </svg>
        <span>555-0184-2760</span>
      </div>
      <div class="web">www.<strong>ridgeviewlawyers</strong>.com</div>
    </footer>
  </main>
</body>
</html>
```